New Business Card Design Project LORVANTI-Italy

we are LORVANTI-Italy
our company in the market for 3 years we are luxury cosmetic company and its about time for a facelift :)
i will like to have elegant luxurious and unique business card
that will give the person that get it a unique, luxurious and elegant impression
I'm VERY OPEN FOR NEW IDEAS , even duo i add a few files of things that i see on line and i like them

i add my logo as well
my website is LORVANTI.COM
(if you would like to see the main style that we have)

Target Market(s)

adult that have money :)

Industry/Entity Type

Business

Contact Information for Business Card

Name - Dario Lorvanti
Position - CEO and CO Founder
address - 4817 E Halvern
telephone - 555-384-1926
email - dario@lorvanti.com
fax - 555-384-1926
website - LORVANTI.COM

Colors
000000
959595
fbee3e
ffffff

Requirements
Must have
• big logo in GOLD color
• elegant look
• impressive
Nice to have
• not must but maybe classy pattern background
• not must but maybe emblem
• maybe clear plastic business card
Should not have
• colors
• images

```html
<!DOCTYPE html>
<html lang="en">
<head>
<meta charset="utf-8">
<title>LORVANTI Italy — Business Card</title>
<link href="https://fonts.googleapis.com/css2?family=Open+Sans:wght@400;600&display=swap" rel="stylesheet">
<style>
  :root {
    --stage: #2a2a2a;
    --gold-light: #ecdc7a;
    --gold: #d6b651;
    --gold-deep: #c9a437;
    --gold-text: #c79f33;
    --ink: #4a4a4a;
    --grey: #959595;
    --paper: #ffffff;
  }
  * { margin: 0; padding: 0; box-sizing: border-box; }
  html, body {
    width: 1200px; height: 900px; overflow: hidden;
    background: var(--stage);
    font-family: "Open Sans", Arial, sans-serif;
  }
  .stage {
    width: 1200px; height: 900px;
    display: flex; flex-direction: column; align-items: center; justify-content: center;
    gap: 44px;
  }
  .card {
    position: relative;
    width: 600px; height: 343px;
    overflow: hidden;
  }

  /* Front */
  .card-front {
    background: linear-gradient(120deg, var(--gold-light) 0%, var(--gold) 45%, var(--gold-deep) 100%);
    color: var(--paper);
    display: flex; flex-direction: column; align-items: center; justify-content: center;
  }
  .brand-mark {
    width: 64px; height: 64px; border-radius: 50%;
    border: 2px solid var(--paper);
    margin-bottom: 14px;
  }
  .brand-name {
    font-size: 34px; font-weight: 400; letter-spacing: 2px; line-height: 1;
  }
  .brand-country {
    font-size: 11px; letter-spacing: 3px; margin-top: 8px;
  }
  .front-web {
    font-size: 12px; letter-spacing: 4px; margin-top: 26px;
  }

  /* Back */
  .card-back { background: var(--paper); }
  .card-back .gold-band {
    position: absolute; left: 0; right: 0; bottom: 0; height: 14px;
    background: linear-gradient(90deg, var(--gold-light), var(--gold-deep));
  }
  .back-logo {
    position: absolute; top: 30px; right: 44px;
    display: flex; flex-direction: column; align-items: center;
    color: var(--gold-text);
  }
  .back-logo .brand-mark {
    width: 50px; height: 50px; border-color: var(--gold-text); margin-bottom: 10px;
  }
  .back-logo .brand-name { font-size: 26px; }
  .back-logo .brand-country { font-size: 9px; margin-top: 6px; }
  .divider {
    position: absolute; left: 36px; right: 36px; top: 152px;
    height: 1px; background: var(--grey);
  }
  .address {
    position: absolute; top: 170px; right: 44px;
    text-align: right; font-size: 12px; line-height: 1.5; color: var(--ink);
  }
  .person {
    position: absolute; left: 44px; bottom: 108px;
  }
  .person-name { font-size: 17px; font-weight: 600; color: var(--gold-text); line-height: 1.3; }
  .person-role { font-size: 12px; color: var(--ink); }
  .person-rule {
    position: absolute; left: 44px; bottom: 96px; width: 170px; height: 1px; background: var(--grey);
  }
  .contacts {
    position: absolute; left: 44px; bottom: 26px;
    list-style: none; font-size: 12px; color: var(--ink); line-height: 1.6;
  }
  .contacts li { display: flex; align-items: center; gap: 8px; }
  .contacts svg { width: 11px; height: 11px; fill: var(--gold-text); }
</style>
</head>
<body>
<main class="stage">
  <section class="card card-front">
    <span class="brand-mark"></span>
    <div class="brand-name">LORVANTI</div>
    <div class="brand-country">ITALY</div>
    <div class="front-web">www.lorvanti.com</div>
  </section>

  <section class="card card-back">
    <div class="back-logo">
      <span class="brand-mark"></span>
      <div class="brand-name">LORVANTI</div>
      <div class="brand-country">ITALY</div>
    </div>
    <div class="divider"></div>
    <address class="address" style="font-style:normal">
      4817 E Halvern<br>WWW.LORVANTI.COM
    </address>

    <div class="person">
      <div class="person-name">Dario Lorvanti</div>
      <div class="person-role">CEO &amp; CO Founder</div>
    </div>
    <div class="person-rule"></div>
    <ul class="contacts">
      <li>
        <svg viewBox="0 0 12 12" aria-hidden="true"><path d="M2 1h2.5l1 3-1.5 1a6 6 0 0 0 3 3l1-1.5 3 1V10a1 1 0 0 1-1 1A9 9 0 0 1 1 2a1 1 0 0 1 1-1z"/></svg>
        555-384-1926
      </li>
      <li>
        <svg viewBox="0 0 12 12" aria-hidden="true"><rect x="3" y="1" width="6" height="3"/><rect x="1" y="4.5" width="10" height="5" rx="1"/><rect x="3" y="8" width="6" height="3"/></svg>
        555-384-1926
      </li>
      <li>
        <svg viewBox="0 0 12 12" aria-hidden="true"><path d="M1 2.5h10v7H1z M1 2.5l5 4 5-4" stroke="#fff" stroke-width="0.8"/></svg>
        dario@lorvanti.com
      </li>
    </ul>
    <div class="gold-band"></div>
  </section>
</main>
</body>
</html>
```